"Velmora Crest" sexual performance enhancement pill bottle label needed.

This should be interesting...

I am starting a line of sexual performance enhancement products. This will be the first of several products basically. Keep in mind, I am the type of business person to stay with one company for years if they provide me with quality work.

This particular product is a male sexual performance pill. The name of the product is "Velmora Crest." The packaging of the pills are a black bottle with a white top. Label on the product example would be perfect but at a minimum I have attached a "template" for your guidance.

Some of the technical aspects of this are as follows:

-File Format: Illustrator CS6 is preferred. (Winner must provide artwork in layer and can not flatten artwork.)
-Resolution: 300 dpi minimum
-Bleed: 1/16th (0.0625") inch from edge of label
-Color Mode: CMYK only or must be converted to CMYK for final production

Lastly, this is your project as a designer, artist, creator, this is essentially a piece of you that will be sold and known by thousands of people. I have no color scheme that I prefer, just use the template and follow the layout. If you have any further questions, please feel free to contact me at any time.
Updates

Quick note on the product and what it does: -Powerful, long lasting, harder erections -Works in a minutes and last for hours -Enhances sexual desire and drive Thank you for your ideas...

Project Deadline Extended
Reason: We decided to extent the project for a few more days to let the last few concepts come in. So far things are looking really good and we definitely have seen some amazing designs. Thank you for your hard work and amazing creativity. Looking forward to seeing what we have come in the next couple of day. Very respectfully, Brev

ONLY THREE DAYS LEFT!!!! Please submit your ideas as soon as possible. And as always, thank you for your help!!! V/r, Brev

Industry/Entity Type

Graphic Design

```html
<!DOCTYPE html>
<html lang="en">
<head>
<meta charset="utf-8">
<title>Velmora Crest – Bottle Label</title>
<link rel="stylesheet" href="https://fonts.googleapis.com/css2?family=Russo+One&family=Teko:wght@600&family=Roboto:wght@400;700&family=Roboto+Condensed:wght@400;700&display=swap">
<style>
  :root {
    --ink: #ffffff;
    --night: #05060c;
    --ember: #ff5a12;
    --ember-soft: #ff8a3d;
    --azure: #1f2bff;
    --azure-deep: #0a0f5a;
    --teal-ink: #0f3b40;
    --silver: #d9d9de;
    --panel: #000000;
  }
  * { margin: 0; padding: 0; box-sizing: border-box; }
  html, body { width: 1200px; height: 556px; overflow: hidden; background: #fff; }
  .label {
    position: relative; width: 1200px; height: 556px; overflow: hidden;
    background:
      radial-gradient(ellipse 260px 320px at 90px 300px, rgba(255,90,18,.35), transparent 70%),
      radial-gradient(ellipse 420px 420px at 900px 260px, rgba(31,43,255,.45), transparent 70%),
      linear-gradient(90deg, var(--night) 0%, #120a08 30%, #0b0c2a 55%, var(--azure-deep) 80%, #060828 100%);
    font-family: "Roboto", Arial, sans-serif; color: var(--ink);
  }
  .top-band {
    position: absolute; left: 0; top: 0; width: 1200px; height: 28px;
    background: linear-gradient(90deg, var(--ember) 0%, #ffe9dc 30%, #ffffff 50%, #ffe9dc 70%, var(--ember) 100%);
    text-align: center;
  }
  .top-band .tagline {
    font-family: "Russo One", sans-serif; font-size: 21px; letter-spacing: 2px;
    color: var(--teal-ink); line-height: 28px;
  }
  .bottom-band {
    position: absolute; left: 0; bottom: 0; width: 1200px; height: 10px;
    background: linear-gradient(90deg, var(--ember), var(--ember-soft), var(--ember));
  }
  .model-photo {
    position: absolute; left: 228px; top: 28px; width: 390px; height: 518px;
    background:
      radial-gradient(ellipse 150px 230px at 170px 250px, rgba(214,160,130,.75), transparent 75%),
      linear-gradient(180deg, rgba(120,90,70,.55) 0%, rgba(90,60,45,.55) 60%, rgba(40,25,20,.2) 100%);
  }
  .side-column {
    position: absolute; left: 10px; top: 152px; width: 278px;
    display: flex; flex-direction: column;
  }
  .directions {
    font-family: "Roboto Condensed", Arial, sans-serif;
    font-size: 9.6px; line-height: 10.9px; text-align: justify;
  }
  .directions p { margin-bottom: 2px; }
  .directions .warning { font-weight: 700; }
  .fda-note {
    margin-top: 6px; width: 276px;
    background: #fff; color: #111; font-size: 8.2px; line-height: 1.2; padding: 4px 6px;
  }
  .maker { margin-top: 20px; padding-left: 5px; font-size: 12px; }
  .maker .lead { font-style: italic; font-weight: 700; }
  .maker .company { font-weight: 700; margin-top: 2px; }
  .brand-name {
    position: absolute; left: 418px; top: 176px;
    font-family: "Teko", sans-serif; font-weight: 600; color: var(--silver);
    font-size: 92px; line-height: 70px; display: flex; align-items: flex-start; gap: 12px;
  }
  .brand-name .mark {
    width: 26px; height: 26px; border-radius: 50%; background: var(--silver); margin-top: 12px;
  }
  .pack-info {
    position: absolute; left: 380px; top: 443px;
    font-family: "Russo One", sans-serif; font-style: italic; color: var(--ink);
  }
  .pack-info .kind { font-size: 20px; line-height: 26px; }
  .pack-info .count { font-size: 29px; line-height: 34px; letter-spacing: 1px; }
  .ribbon { position: absolute; left: 590px; top: 320px; }
  .facts {
    position: absolute; left: 885px; top: 144px; width: 306px; height: 270px;
    background: var(--panel); border: 1px solid #cfcfcf; padding: 6px 10px;
  }
  .facts h2 { font-weight: 400; font-size: 29px; line-height: 32px; }
  .facts .serving { font-weight: 700; font-size: 12.5px; line-height: 17px; }
  .facts .rule-thick { border-top: 6px solid #fff; margin: 4px 0 5px; }
  .facts .rule { border-top: 1px solid #fff; margin: 4px 0; }
  .facts .head-row, .facts .formula-row {
    display: flex; justify-content: space-between; font-size: 12px;
  }
  .facts .formula-row { font-weight: 700; font-size: 11px; margin-top: 3px; }
  .facts .ingredients { font-size: 10.8px; line-height: 1.32; text-align: justify; }
  .facts .rule-mid { border-top: 4px solid #fff; margin: 6px 0 4px; }
  .facts .footnote { font-weight: 700; font-size: 12px; }
  .other-ingredients {
    position: absolute; left: 892px; top: 424px; width: 300px; font-size: 10.5px; line-height: 1.3;
  }
  .other-ingredients b { font-weight: 700; }
</style>
</head>
<body>
<main class="label">
  <header class="top-band"><span class="tagline">Enhances sexual desire</span></header>

  <div class="model-photo" role="img" aria-label="Photograph of a woman with long blonde hair, posed facing the viewer"></div>

  <div class="side-column">
    <section class="directions">
      <p>SUGGESTED USE: As a dietary supplement, take two (2) capsules 1 hour before physical activity, or as directed by your health care professional. Do not exceed two (2) capsules daily.</p>
      <p>CAUTION: Do not exceed recommended dose. This product is not intended for pregnant or nursing mothers, children under the age of 18, or individuals taking prescription drugs. Discontinue use immediately if nausea, sleeplessness, or nervousness occur. Do not take this product if you have a known medical condition including high blood pressure, diabetes, any cardiovascular disorder, heart disease, hyperthyroidism, or are taking anti-depressant medications. If you have questions about the advisability of taking this product, consult your physician prior to use.</p>
      <p class="warning">KEEP OUT OF THE REACH OF CHILDREN. DO NOT USE IF SAFETY SEAL IS DAMAGED OR MISSING. STORE AT ROOM TEMPERATURE.</p>
    </section>

    <p class="fda-note">* These statements have not been evaluated by the Food and Drug Administration. This product is not intended to diagnose, treat, cure or prevent any disease.</p>

    <div class="maker">
      <p class="lead">Manufactured Exclusively For:</p>
      <p class="company">COMPANY INFO</p>
    </div>
  </div>

  <h1 class="brand-name"><span>Velmora<br>Crest</span><span class="mark"></span></h1>

  <div class="pack-info">
    <p class="kind">Dietary Supplement</p>
    <p class="count">60 Capsules</p>
  </div>

  <svg class="ribbon" width="290" height="230" viewBox="0 0 290 230">
    <defs>
      <linearGradient id="ribbonMetal" x1="0" y1="0" x2="1" y2="1">
        <stop offset="0" stop-color="#f2f2f4"/>
        <stop offset=".5" stop-color="#b8b8be"/>
        <stop offset="1" stop-color="#7c7c84"/>
      </linearGradient>
    </defs>
    <polygon points="210,0 290,0 80,230 0,230" fill="url(#ribbonMetal)"/>
    <g transform="translate(150,118) rotate(-47)" font-family="Russo One, sans-serif" fill="#2b2b30" text-anchor="middle">
      <text y="-4" font-size="21">REACH YOUR PEAK</text>
      <text y="22" font-size="23">PERFORMANCE</text>
    </g>
  </svg>

  <section class="facts">
    <h2>Supplement Facts</h2>
    <p class="serving">Serving Size: 2 Capsules</p>
    <p class="serving">Servings Per Container: 30</p>
    <div class="rule-thick"></div>
    <div class="head-row"><span>Amount Per Serving</span><span>% Daily Value</span></div>
    <div class="rule"></div>
    <div class="formula-row"><span>VLC-Rx™ Proprietary Formula</span><span>1,560 mg &nbsp;†</span></div>
    <p class="ingredients">Horny Goat Weed (herb powder), Maca (herb powder), Macuna Pruriens (L-Dopa), Polypodium Vulgare (herb powder), Yohimbe Bark (herb powder), Saw Palmetto (herb powder), Muira Puama (herb powder), Arginine (L-Arginine hydrochloride), Panax Ginseng (herb powder)</p>
    <div class="rule-mid"></div>
    <p class="footnote">† % Daily Value not established</p>
  </section>

  <p class="other-ingredients"><b>Other Ingredients:</b> Gelatin, Magnesium Stearate, and Calcium Carbonate.</p>

  <footer class="bottom-band"></footer>
</main>
</body>
</html>
```